Dental Savings Plan - Raymond Castell DDS

We need a tri-fold brochure and 1 page flyer/poster for Dr. Raymond Castell' dental office located on Maui, Hawaii. We are offering a new "Dental Savings Plan" to patients.
I have included 3 photos, along with the office logo. You do not have to use all photos if you do not want to. We want this to catch the eyes of patients, easy for them to read and understand, and to show them that this is a much better option than dental insurance.
Please use same Hawaiian theme and colors on the office website https://www.brightcoveclinic.com .

Please also include the following to promote this new plan:

Dental Services Include
• Professional Dental Cleanings (2 per benefit year)
• Perio Maintenance Cleanings (3 per benefit year) covered at 80%
• Radiographs as needed (1 set of X-rays per benefit year)
• Doctor Examinations (2 per benefit year)
• Ozone Treatment
• BRISK Amalgam Removal
• Additional limited/emergency exam (1 per benefit year)
• Cosmetic consultation
• 15% discount on all other services (including cosmetic procedures)
• 10% discount on implants and implant crowns

Advantages of the Dental Savings Plan
1. No deductibles
2. No waiting periods
3. No claims to file
4. No frequency limitations or exclusions
5. No yearly maximum benefits
6. No pre-authorization requirements
7. No pre-existing conditions limitations
8. State of the art facility and technology
9. Immediate enrollment
10. Highest quality of care for you and your Ohana

Annual Fee
$399 first family member/individual (equivalent to $33 per month)
$349 second family member (equivalent to $29 per month)
$249 each additional family member (equivalent to $20 per month)

Provisions of the Dental Savings Plan
• May not be combined with insurance plans, discounts or promotions
• This Dental Savings Plan is not an insurance plan, but a payment arrangement provided by Raymond Castell DDS, and is not transferable to any other dental office or dental specialist
• Payment for services are due at the date of service
• This program is for you and is not transferable
• Benefits are provided for one year from the date the plan is purchased
• Must be paid in full when starting the plan
• No refunds will be provided for dues of the plan annual fee under any circumstances, including failure to schedule and maintain appointments
• If Pay Ladder is used to pay for the program and for services then only a 10% discount will be given
• To receive the full 15% discount on restorative treatment, you must schedule the appointment the day it is recommended. Any failed appointment results in the loss of the 15% discount.

Target Market(s)

Dental patients without dental insurance

Industry/Entity Type

Dental Clinic

Requirements
Must have
• My project must have the logo file to identify the dental office, Hawaiian theme, same colors as website, match style of website font, theme and colors, as well as, all the Dental Services, Advantages of the Dental Savings Plan, Annual Fee, and the Provisions of the Dental Savings Plan.

```html
<!DOCTYPE html>
<html lang="en">
<head>
<meta charset="utf-8">
<title>Dental Savings Plan – Bright Cove Smiles</title>
<link href="https://fonts.googleapis.com/css2?family=Cinzel:wght@900&family=PT+Sans:wght@400;700&display=swap" rel="stylesheet">
<style>
  :root{
    --blue:#2a93c8;
    --blue-light:#5bbbe6;
    --green:#8cc63f;
    --green-dark:#5e9c26;
    --title-green:#9bcb3c;
    --white:#ffffff;
  }
  *{box-sizing:border-box;margin:0;padding:0}
  html,body{width:1000px;height:1200px;overflow:hidden;background:var(--white)}
  body{font-family:"PT Sans",Arial,sans-serif;color:var(--white);position:relative}

  .hero{position:absolute;left:0;top:0;width:1000px;height:400px;overflow:hidden}
  .hero-photo{position:absolute;inset:0;
    background:
      radial-gradient(ellipse 150px 210px at 850px 190px, rgba(214,168,140,.85), rgba(214,168,140,0) 70%),
      radial-gradient(ellipse 220px 290px at 860px 220px, rgba(90,70,60,.55), rgba(90,70,60,0) 75%),
      linear-gradient(100deg,#e9eef1 0%,#c9d3d8 30%,#8a9ca6 55%,#7b96a6 75%,#a9b9c2 100%);}
  .hero-shade{position:absolute;left:0;top:170px;width:720px;height:230px;
    background:linear-gradient(180deg,rgba(40,55,65,0) 0%,rgba(40,55,65,.55) 40%,rgba(40,55,65,.6) 100%)}

  .brand{position:absolute;left:72px;top:132px;display:flex;align-items:center;gap:10px}
  .brand-dot{width:13px;height:13px;border-radius:50%;background:var(--blue)}
  .brand-name{font-size:20px;font-weight:400;color:var(--blue)}

  .title{position:absolute;left:310px;top:76px;width:370px;font-family:"Cinzel",Georgia,serif;font-weight:900;
    font-size:42px;line-height:50px;color:var(--title-green);text-align:center;
    text-shadow:2px 2px 3px rgba(30,40,20,.75)}

  .fees{position:absolute;left:24px;top:200px}
  .fees h2{font-size:25px;font-weight:700;color:var(--title-green);letter-spacing:.3px;margin-bottom:4px}
  .fees ul{list-style:none}
  .fees li{font-size:17.5px;line-height:26px;padding-left:26px;position:relative}

  .fees li::before,.advantages li::before{content:"";position:absolute;left:0;top:7px;width:12px;height:12px;
    border:1.5px solid var(--green);border-radius:50%}
  .fees li::after,.advantages li::after{content:"";position:absolute;left:4px;top:9.5px;width:3px;height:5px;
    border:solid var(--green);border-width:0 1.5px 1.5px 0;transform:rotate(45deg)}

  .wave{position:absolute;left:0;top:320px;width:1000px;height:90px}

  .panel{position:absolute;top:471px;width:312px;height:562px;background:var(--blue);border-radius:12px;
    box-shadow:0 6px 10px rgba(0,0,0,.25);padding:66px 16px 16px}
  .panel-services{left:20px}
  .panel-advantages{left:344px}
  .panel-provisions{left:668px}
  .panel h3{font-size:22px;line-height:27px;font-weight:700;text-align:center;margin-bottom:16px;letter-spacing:.2px}

  .badge{position:absolute;top:-56px;left:50%;transform:translateX(-50%);width:106px;height:106px;border-radius:50%;
    background:var(--green);display:flex;align-items:center;justify-content:center}
  .badge-inner{width:90px;height:90px;border-radius:50%;background:var(--blue-light);border:3px solid var(--white);
    display:flex;align-items:center;justify-content:center;color:var(--white);font-size:40px}

  .services ul{list-style:none;padding-left:4px}
  .services li{font-size:15px;line-height:19px;padding-left:12px;position:relative;margin-bottom:3px}
  .services li::before{content:"•";position:absolute;left:0;top:0}
  .services small{display:block;font-size:11px;line-height:14px}

  .discounts{display:flex;gap:10px;margin-top:16px;padding:0 4px}
  .discount{flex:1;border:2px solid var(--green);padding:8px 4px;text-align:center}
  .discount strong{display:block;font-size:18px;font-weight:400;line-height:21px}
  .discount span{display:block;font-size:11px;line-height:13px}
  .discount em{display:block;font-style:normal;font-size:8px;line-height:10px}

  .advantages ul{list-style:none;padding-left:4px}
  .advantages li{font-size:15px;line-height:30px;padding-left:22px;position:relative}
  .advantages li::before{top:9px}
  .advantages li::after{top:11.5px}

  .provisions ul{list-style:none}
  .provisions li{font-size:13px;line-height:14.6px;padding-left:10px;position:relative;margin-bottom:5px;text-align:justify}
  .provisions li::before{content:"";position:absolute;left:0;top:5px;width:5px;height:5px;border-radius:50%;background:var(--green)}

  .couple{position:absolute;left:-6px;top:982px;width:262px;height:262px;border-radius:50%;border:4px solid var(--white);
    background:
      radial-gradient(ellipse 90px 70px at 130px 100px, rgba(222,176,148,.9), rgba(222,176,148,0) 70%),
      linear-gradient(180deg,#7fc4e6 0%,#a7d8ee 45%,#3ea3c9 62%,#e6dcc7 80%,#d9ccb2 100%);
    box-shadow:0 2px 6px rgba(0,0,0,.25);z-index:2}

  .footer{position:absolute;left:0;top:1094px;width:1000px;height:106px;
    background:linear-gradient(90deg,#ffffff 0%,#cfe8a9 25%,var(--green) 55%,var(--green-dark) 100%);
    color:var(--white);padding:12px 14px 0 0;font-size:15px;line-height:27px}
  .footer p{display:flex;justify-content:flex-end;align-items:center;gap:8px}
  .footer svg{width:20px;height:20px}
</style>
</head>
<body>

<header class="hero">
  <div class="hero-photo" role="img" aria-label="Photo of a smiling young woman with long brown hair in soft sunlight"></div>
  <div class="hero-shade"></div>
  <div class="brand">
    <span class="brand-dot"></span>
    <span class="brand-name">Bright Cove Smiles</span>
  </div>
  <h1 class="title">DENTAL<br>SAVINGS PLAN</h1>
  <section class="fees">
    <h2>ANNUAL FEE</h2>
    <ul>
      <li>$399 first family member/individual (equivalent to $33 per month)</li>
      <li>$349 second family member (equivalent to $29 per month)</li>
      <li>$249 each additional family member (equivalent to $20 per month)</li>
    </ul>
  </section>
</header>

<svg class="wave" viewBox="0 0 1000 90" preserveAspectRatio="none" aria-hidden="true">
  <path d="M0 18 C280 80 640 80 1000 14 L1000 90 L0 90 Z" fill="#ffffff"/>
  <path d="M0 18 C280 80 640 80 1000 14" fill="none" stroke="#8cc63f" stroke-width="5"/>
</svg>

<section class="panel panel-services services">
  <div class="badge"><div class="badge-inner">
    <svg width="44" height="50" viewBox="0 0 44 50" fill="none" stroke="#fff" stroke-width="3" stroke-linejoin="round" aria-hidden="true">
      <path d="M12 3c-6 0-9 5-9 11 0 8 4 12 5 20 1 8 3 13 6 13 3 0 3-10 8-10s5 10 8 10c3 0 5-5 6-13 1-8 5-12 5-20 0-6-3-11-9-11-4 0-6 2-10 2s-6-2-10-2z"/>
    </svg>
  </div></div>
  <h3>DENTAL SERVICES<br>INCLUDE</h3>
  <ul>
    <li>Professional Dental Cleanings<small>(2 per benefit year)</small></li>
    <li>Perio Maintenance Cleanings<small>(3 per benefit year) covered at 80%</small></li>
    <li>Radiographs as needed<small>(1 set of X-rays per benefit year)</small></li>
    <li>Doctor Examinations<small>(2 per benefit year)</small></li>
    <li>Ozone Treatment</li>
    <li>BRISK Amalgam Removal</li>
    <li>Additional limited/emergency exam<small>(1 per benefit year)</small></li>
    <li>Cosmetic consultation</li>
  </ul>
  <div class="discounts">
    <div class="discount"><strong>15% discount</strong><span>on all other services</span><em>(including cosmetic procedures)</em></div>
    <div class="discount"><strong>10% discount</strong><span>on implants and<br>implant crowns</span></div>
  </div>
</section>

<section class="panel panel-advantages advantages">
  <div class="badge"><div class="badge-inner">
    <svg width="44" height="44" viewBox="0 0 44 44" aria-hidden="true">
      <path d="M20 6 A17 17 0 1 0 37 24 L20 24 Z" fill="#fff"/>
      <path d="M24 2 A17 17 0 0 1 41 19 L24 19 Z" fill="#fff"/>
      <text x="13" y="31" font-family="PT Sans,Arial,sans-serif" font-size="16" font-weight="700" fill="#5bbbe6">$</text>
    </svg>
  </div></div>
  <h3>ADVANTAGES OF THE<br>DENTAL SAVINGS PLAN</h3>
  <ul>
    <li>No deductibles</li>
    <li>No waiting periods</li>
    <li>No claims to file</li>
    <li>No frequency limitations or<br>exclusions</li>
    <li>No yearly maximum benefits</li>
    <li>No pre-authorization requirements</li>
    <li>No pre-existing conditions limitations</li>
    <li>State of the art facility &amp; technology</li>
    <li>Immediate enrollment</li>
    <li>Highest quality of care for you and<br>your Ohana</li>
  </ul>
</section>

<section class="panel panel-provisions provisions">
  <div class="badge"><div class="badge-inner">%</div></div>
  <h3>PROVISIONS OF THE<br>DENTAL SAVINGS PLAN</h3>
  <ul>
    <li>May not be combined with insurance plans, discounts or promotions</li>
    <li>This Dental Savings Plan is not an insurance plan, but a payment arrangement provided by Bright Cove Smiles, and is not transferable to any other dental office or dental specialist</li>
    <li>Payment for services are due at the date of service</li>
    <li>This program is for you and is not transferable</li>
    <li>Benefits are provided for one year from the date the plan is purchased</li>
    <li>Must be paid in full when starting the plan</li>
    <li>No refunds will be provided for dues of the plan annual fee under any circumstances, including failure to schedule and maintain appointments</li>
    <li>If Pay Ladder is used to pay for the program and for services then only a 10% discount will be given</li>
    <li>To receive the full 15% discount on restorative treatment, you must schedule the appointment the day it is recommended. Any failed appointment results in the loss of the 15% discount.</li>
  </ul>
</section>

<div class="couple" role="img" aria-label="Photo of a laughing couple on a sunny beach, the woman riding piggyback"></div>

<footer class="footer">
  <p>808-555-0142
    <svg viewBox="0 0 20 20" aria-hidden="true"><circle cx="10" cy="10" r="8.5" fill="none" stroke="#fff" stroke-width="1.5"/><path d="M7 5.5l1.6 2.4-1 1.2c.6 1.3 1.5 2.2 2.8 2.8l1.2-1 2.4 1.6-.8 1.8c-3.6-.2-6.8-3.4-7-7z" fill="#fff"/></svg>
  </p>
  <p>www.brightcoveclinic.com &nbsp;|&nbsp; hello@brightcoveclinic.com
    <svg viewBox="0 0 20 20" aria-hidden="true"><circle cx="10" cy="10" r="8.5" fill="none" stroke="#fff" stroke-width="1.5"/><circle cx="10" cy="10" r="2.6" fill="none" stroke="#fff" stroke-width="1.5"/><path d="M12.6 8v3c0 1.4 2 1.4 2 0v-1a4.6 4.6 0 1 0-2 3.8" fill="none" stroke="#fff" stroke-width="1.5"/></svg>
  </p>
  <p>2470 Makai Shore Rd # 112, Kihei, HI 96753
    <svg viewBox="0 0 20 20" aria-hidden="true"><circle cx="10" cy="10" r="8.5" fill="none" stroke="#fff" stroke-width="1.5"/><path d="M10 15s-3.5-3.6-3.5-6a3.5 3.5 0 0 1 7 0c0 2.4-3.5 6-3.5 6z" fill="#fff"/><circle cx="10" cy="9" r="1.2" fill="#6aa72b"/></svg>
  </p>
</footer>

</body>
</html>
```